Salon and Spa Distributor Business Card

Need a business card. We are are distributor in the salon and spa industry. We identify with natural beauty. Need a card with:
Company Name: Petal Quarry"
Title: "President & CEO"
Address
Company Phone number
email
website
Tag Line:" The Professional Salon Source"

Industry/Entity Type

Business

Contact Information for Business Card

Name: Dov Strommen
Title: "President & CEO"
Address: 31 Harlow Ln, Bexmoor, NJ 07813
Company Phone number: 800-463-5918
email: dovstrommen@petalquarry.example
website: www.petalquarry.example

Requirements
Should not have
• No black backgrounds

```html
<!DOCTYPE html>
<html lang="en">
<head>
<meta charset="utf-8">
<title>Petal Quarry – Business Card</title>
<link href="https://fonts.googleapis.com/css2?family=Questrial&display=swap" rel="stylesheet">
<style>
  :root {
    --backdrop: #232323;
    --green-light: #67bb47;
    --green-mid: #3f9a3e;
    --green-deep: #0d6534;
    --brand-green: #4a9a3f;
    --ink: #1b1b1b;
    --paper: #ffffff;
  }
  * { margin: 0; padding: 0; box-sizing: border-box; }
  html, body {
    width: 1189px; height: 1200px; overflow: hidden;
    background: var(--backdrop);
    font-family: "Questrial", "Century Gothic", sans-serif;
  }
  .card {
    position: absolute; left: 171px; width: 856px; height: 487px;
    border-radius: 22px; overflow: hidden;
    box-shadow: 0 4px 8px rgba(0,0,0,0.45);
  }
  .text { position: absolute; line-height: 1; white-space: nowrap; }

  /* front */
  .card--front {
    top: 68px;
    background: linear-gradient(180deg, var(--green-light) 0%, var(--green-mid) 45%, var(--green-deep) 100%);
    color: var(--paper);
  }
  .front__dot {
    position: absolute; left: 176px; top: 128px; width: 38px; height: 38px;
    border-radius: 50%; background: var(--paper);
  }
  .front__name { left: 235px; top: 122px; font-size: 47px; }
  .front__tagline { left: 236px; top: 176px; font-size: 21px; }
  .front__web { left: 41px; top: 412px; font-size: 22px; }

  /* back */
  .card--back { top: 626px; background: var(--paper); color: var(--ink); }
  .back__motif {
    position: absolute; left: 0; top: 0; width: 360px; height: 487px;
    background: radial-gradient(ellipse at 35% 55%, rgba(103,187,71,0.55) 0%, rgba(63,154,62,0.25) 45%, rgba(255,255,255,0) 75%);
  }
  .back__name { left: 454px; top: 61px; font-size: 54px; color: var(--brand-green); }
  .back__tagline { left: 455px; top: 116px; font-size: 22px; }
  .back__person { left: 454px; top: 208px; font-size: 31px; color: var(--brand-green); }
  .back__title { left: 454px; top: 241px; font-size: 22px; }
  .back__address { left: 454px; top: 296px; font-size: 22px; line-height: 29px; }
  .contact { position: absolute; left: 459px; display: flex; align-items: center; gap: 12px; font-size: 22px; line-height: 1; }
  .contact svg { width: 22px; height: 22px; flex: none; }
  .contact--phone { top: 366px; }
  .contact--email { top: 393px; }
  .contact--web { top: 421px; }
</style>
</head>
<body>
  <section class="card card--front">
    <span class="front__dot"></span>
    <div class="text front__name">Petal Quarry</div>
    <div class="text front__tagline">The Professional Salon Source</div>
    <div class="text front__web">www.petalquarry.example</div>
  </section>

  <section class="card card--back">
    <div class="back__motif" role="img" aria-label="Soft green decorative leaf and flowing hair motif"></div>
    <div class="text back__name">Petal Quarry</div>
    <div class="text back__tagline">The Professional Salon Source</div>
    <div class="text back__person">Dov Strommen</div>
    <div class="text back__title">President &amp; CEO</div>
    <div class="text back__address">31 Harlow Ln,<br>Bexmoor, NJ 07813</div>

    <div class="contact contact--phone">
      <svg viewBox="0 0 22 22" aria-hidden="true">
        <rect width="22" height="22" rx="3" fill="#3f9a3e"/>
        <path d="M5 9c0-3 3-4 6-4s6 1 6 4l-2 1-1-2h-6l-1 2z" fill="#fff"/>
        <rect x="6" y="11" width="10" height="6" rx="1" fill="#fff"/>
      </svg>
      <span>800-463-5918</span>
    </div>
    <div class="contact contact--email">
      <svg viewBox="0 0 22 22" aria-hidden="true">
        <rect width="22" height="22" rx="3" fill="#3f9a3e"/>
        <rect x="4" y="6" width="14" height="10" fill="none" stroke="#fff" stroke-width="1.5"/>
        <path d="M4 6l7 6 7-6" fill="none" stroke="#fff" stroke-width="1.5"/>
      </svg>
      <span>dovstrommen@petalquarry.example</span>
    </div>
    <div class="contact contact--web">
      <svg viewBox="0 0 22 22" aria-hidden="true">
        <rect width="22" height="22" rx="3" fill="#3f9a3e"/>
        <g fill="none" stroke="#fff" stroke-width="1.2">
          <circle cx="11" cy="11" r="6.5"/>
          <ellipse cx="11" cy="11" rx="3" ry="6.5"/>
          <path d="M4.5 11h13M5.5 7.5h11M5.5 14.5h11"/>
        </g>
      </svg>
      <span>www.petalquarry.example</span>
    </div>
  </section>
</body>
</html>
```